Animal Eye Clinic needs a Business card

We are a new veterinary ophthalmology practice (Ridgeline Pet Vision Care) and we need a business card designed. We only see animal eyes - we are not a regular veterinary clinic. We already have a logo. We are looking for a professional, good looking business card to hand out to our clients. We are looking for something simple but professional and contemporary. Our logo is likely the only picture/graphic that needs to be on the card.
Updates

Contact Information for Business Card

Delia Vossman, BSc, DVM, MSc, DipACVO
Veterinary Ophthalmologist

Phone: 250.418.3927
Email: ridgelinepetvisioncare@mailbox-example.net
Website: ridgelinepetvisioncare-example.net
Address: 1874 Thornbury Rd
Kelowna, BC, V1X 4M9

Colors

Designer to choose colors to be used in the design.

Requirements
Must have
• Our logo (attached)

```html
<!DOCTYPE html>
<html lang="en">
<head>
<meta charset="utf-8">
<title>Ridgeline Pet Vision Care – Business Card</title>
<link rel="stylesheet" href="https://fonts.googleapis.com/css2?family=Open+Sans:wght@400;600;700&display=swap">
<style>
  :root {
    --teal: #0a97a9;
    --ink: #1d1e20;
    --paper: #ffffff;
    --stone: #8b8b8b;
    --light-text: #e6e6e6;
    --backdrop: #d9d9d9;
  }
  * { box-sizing: border-box; margin: 0; padding: 0; }
  html, body { width: 1200px; height: 800px; overflow: hidden; }
  body {
    background: var(--backdrop);
    font-family: "Open Sans", Arial, sans-serif;
    display: flex;
    align-items: center;
    justify-content: center;
    gap: 40px;
  }
  .card {
    position: relative;
    width: 540px;
    height: 309px;
    overflow: hidden;
    box-shadow: 0 6px 18px rgba(0,0,0,0.18);
  }

  /* Front side */
  .card--front { background: var(--ink); color: var(--light-text); }
  .brand-art {
    position: absolute;
    left: -40px;
    bottom: -70px;
    width: 300px;
    height: 300px;
    border-radius: 50%;
    background: var(--teal);
  }
  .card--front .brand-name {
    position: absolute;
    top: 36px;
    right: 34px;
    font-size: 22px;
    font-weight: 700;
    color: var(--teal);
    letter-spacing: 0.5px;
  }
  .contact {
    position: absolute;
    left: 290px;
    top: 112px;
    right: 20px;
    font-size: 10.5px;
    line-height: 1.55;
  }
  .contact__name {
    font-size: 14px;
    font-weight: 700;
    color: var(--teal);
  }
  .contact__creds { font-size: 9px; font-weight: 600; }
  .contact__title { color: var(--stone); font-size: 11px; margin-bottom: 4px; }
  .contact__row { display: flex; align-items: center; gap: 6px; }
  .contact__row svg { width: 10px; height: 10px; flex: none; }

  /* Back side */
  .card--back { background: var(--paper); }
  .back-lockup {
    position: absolute;
    top: 105px;
    left: 0; right: 0;
    display: flex;
    align-items: center;
    justify-content: center;
    gap: 14px;
  }
  .back-lockup__dot {
    width: 40px; height: 40px;
    border-radius: 50%;
    background: var(--teal);
  }
  .card--back .brand-name {
    font-size: 27px;
    font-weight: 700;
    color: var(--teal);
  }
  .back-url {
    position: absolute;
    bottom: 52px;
    left: 0; right: 0;
    text-align: center;
    font-size: 12px;
    letter-spacing: 3px;
    color: #555;
  }
</style>
</head>
<body>
  <section class="card card--front">
    <div class="brand-art" role="img" aria-label="Brand illustration area in the practice teal"></div>
    <p class="brand-name">Ridgeline Pet Vision Care</p>
    <div class="contact">
      <p class="contact__name">Delia Vossman, <span class="contact__creds">BSc, DVM, MSc, DipACVO</span></p>
      <p class="contact__title">Veterinary Ophthalmologist</p>
      <p>1874 Thornbury Rd Kelowna, BC, V1X 4M9</p>
      <p class="contact__row">
        <svg viewBox="0 0 10 10" aria-hidden="true"><path d="M2 1l2 2-1 1.2c.6 1.2 1.6 2.2 2.8 2.8L7 6l2 2-1.2 1.2C4.5 9 1 5.5.8 2.2z" fill="var(--teal)"/></svg>
        250.418.3927
      </p>
      <p class="contact__row">
        <svg viewBox="0 0 10 10" aria-hidden="true"><rect x="0.5" y="2" width="9" height="6" fill="var(--teal)"/><path d="M0.5 2l4.5 3.5L9.5 2" stroke="var(--ink)" stroke-width="0.8" fill="none"/></svg>
        ridgelinepetvisioncare@mailbox-example.net
      </p>
      <p class="contact__row">
        <svg viewBox="0 0 10 10" aria-hidden="true"><circle cx="5" cy="5" r="4.3" fill="none" stroke="var(--teal)" stroke-width="1.1"/><path d="M0.7 5h8.6M5 0.7c-2.2 2.5-2.2 6.1 0 8.6M5 0.7c2.2 2.5 2.2 6.1 0 8.6" stroke="var(--teal)" stroke-width="0.8" fill="none"/></svg>
        ridgelinepetvisioncare-example.net
      </p>
    </div>
  </section>

  <section class="card card--back">
    <div class="back-lockup">
      <span class="back-lockup__dot" aria-hidden="true"></span>
      <p class="brand-name">Ridgeline Pet Vision Care</p>
    </div>
    <p class="back-url">www.ridgelinepetvisioncare-example.net</p>
  </section>
</body>
</html>
```